Luxury Business Card Design for High-End Window Treatments

Gilded Slatworks
Custom Plantation Shutters & Architectural Shading Systems

⸻

BACK

Daniel Trevick
Owner

Custom Interior & Exterior Window Treatments

919-555-0148
gildedslatworks.com

I have included a picture that I’m hoping we can use on the back, but I’m also wondering if you can get rid of the ladder? Should we get rid of shutters , shades and blinds underneath Gilded Slatworks?

Target Market(s)

High-end residential homeowners, custom home builders, architects, interior designers, and luxury renovation clients seeking premium plantation shutters and motorized architectural shading systems.

Industry/Entity Type

Custom Window treatments

Contact Information for Business Card

Front Gilded Slatworks Custom Plantation Shutters Motorized Architectural Shading Systems BACK Daniel Trevick Owner 919-555-0148 GildedSlatworks.com Custom Interior & Exterior Window Treatments By Appointment

Requirements
Nice to have
• Not 100% sure on nice to halves or the color but you can definitely check out my website to get a better understanding of what I’m trying to do

```html
<!DOCTYPE html>
<html lang="en">
<head>
<meta charset="utf-8">
<title>Gilded Slatworks – Business Card</title>
<link rel="stylesheet" href="https://fonts.googleapis.com/css2?family=Cormorant+Garamond:wght@500;600&family=Zilla+Slab:wght@700&family=Poppins:wght@400;500&display=swap">
<style>
  :root {
    --page-bg: #e7e4df;
    --card-black: #050505;
    --card-white: #ffffff;
    --gold: #c2a550;
    --gold-band: #b9a351;
    --ink: #111111;
    --text-light: #f4f1ea;
    --photo-dark: #4c5563;
    --photo-mid: #8a929c;
  }
  * { box-sizing: border-box; margin: 0; padding: 0; }
  html, body {
    width: 1200px; height: 900px; overflow: hidden;
    background: var(--page-bg);
  }
  .canvas {
    width: 1200px; height: 900px;
    display: flex; flex-direction: column;
    align-items: center; justify-content: center; gap: 48px;
  }
  .card {
    position: relative;
    width: 660px; height: 377px;
    overflow: hidden;
    box-shadow: 0 6px 18px rgba(0,0,0,0.18);
  }

  /* Front */
  .card-front { background: var(--card-black); }
  .brand-name {
    position: absolute; right: 56px; top: 58px;
    font-family: "Cormorant Garamond", serif;
    font-weight: 600; font-size: 66px; line-height: 0.95;
    color: var(--gold); text-align: right;
  }
  .service-list {
    position: absolute; left: 44px; bottom: 40px;
    list-style: none;
    font-family: "Cormorant Garamond", serif;
    font-weight: 600; font-size: 21px; line-height: 1.22;
    color: var(--text-light);
  }
  .service-list li { display: flex; align-items: center; gap: 10px; }
  .service-list li:nth-child(2) { padding-left: 8px; }
  .service-list li:nth-child(3) { padding-left: 16px; }
  .bullet-icon { width: 14px; height: 14px; flex: none; }

  /* Back */
  .card-back { background: var(--card-white); }
  .porch-photo {
    position: absolute; right: 0; top: 0;
    width: 440px; height: 250px;
    background: linear-gradient(to right, rgba(255,255,255,1) 0%, rgba(180,186,194,0.55) 35%, var(--photo-mid) 60%, var(--photo-dark) 100%);
  }
  .wave { position: absolute; left: 0; top: 0; width: 660px; height: 377px; }
  .person-name {
    position: absolute; left: 44px; top: 88px;
    font-family: "Zilla Slab", serif; font-weight: 700;
    font-size: 30px; color: var(--gold);
  }
  .person-role {
    position: absolute; left: 46px; top: 124px;
    font-family: "Poppins", sans-serif; font-weight: 400;
    font-size: 17px; color: var(--ink);
  }
  .contact-list {
    position: absolute; left: 46px; top: 196px;
    list-style: none;
    font-family: "Poppins", sans-serif; font-weight: 400;
    font-size: 18px; line-height: 1.55; color: var(--ink);
  }
  .contact-list li { display: flex; align-items: center; gap: 10px; }
  .contact-icon { width: 18px; height: 18px; flex: none; }
  .tagline {
    position: absolute; right: 32px; bottom: 36px;
    font-family: "Cormorant Garamond", serif; font-weight: 600;
    font-size: 19px; line-height: 1.2; color: var(--gold);
    text-align: right;
  }
</style>
</head>
<body>
<main class="canvas">

  <section class="card card-front" aria-label="Card front">
    <h1 class="brand-name">Gilded<br>Slatworks</h1>
    <ul class="service-list">
      <li><svg class="bullet-icon" viewBox="0 0 14 14"><circle cx="7" cy="7" r="5.5" fill="none" stroke="var(--gold)" stroke-width="1.5"/><circle cx="7" cy="7" r="2" fill="var(--gold)"/></svg>Gilded Slatworks Custom</li>
      <li><svg class="bullet-icon" viewBox="0 0 14 14"><circle cx="7" cy="7" r="5.5" fill="none" stroke="var(--gold)" stroke-width="1.5"/><circle cx="7" cy="7" r="2" fill="var(--gold)"/></svg>Plantation Shutters Motorized</li>
      <li><svg class="bullet-icon" viewBox="0 0 14 14"><circle cx="7" cy="7" r="5.5" fill="none" stroke="var(--gold)" stroke-width="1.5"/><circle cx="7" cy="7" r="2" fill="var(--gold)"/></svg>Architectural Shading Systems</li>
    </ul>
  </section>

  <section class="card card-back" aria-label="Card back">
    <div class="porch-photo" role="img" aria-label="Photo of a home's covered porch with white columns and exterior shades, fading into white"></div>
    <svg class="wave" viewBox="0 0 660 377" aria-hidden="true">
      <path d="M0 288 C230 300 370 258 480 182 L500 190 C400 256 230 312 0 306 Z" fill="var(--gold-band)"/>
      <path d="M0 304 C230 312 400 256 505 188 C565 152 615 142 660 136 L660 377 L0 377 Z" fill="var(--card-black)"/>
    </svg>
    <h2 class="person-name">Daniel Trevick</h2>
    <p class="person-role">Owner</p>
    <ul class="contact-list">
      <li><svg class="contact-icon" viewBox="0 0 24 24"><path d="M6.6 10.8a15 15 0 0 0 6.6 6.6l2.2-2.2a1 1 0 0 1 1-.25 11 11 0 0 0 3.6.6 1 1 0 0 1 1 1V20a1 1 0 0 1-1 1A17 17 0 0 1 3 4a1 1 0 0 1 1-1h3.5a1 1 0 0 1 1 1 11 11 0 0 0 .6 3.6 1 1 0 0 1-.25 1Z" fill="var(--gold)"/></svg>919-555-0148</li>
      <li><svg class="contact-icon" viewBox="0 0 24 24" fill="none" stroke="var(--gold)" stroke-width="2"><circle cx="12" cy="12" r="9.5"/><ellipse cx="12" cy="12" rx="4" ry="9.5"/><path d="M2.5 12h19M4 7h16M4 17h16"/></svg>GildedSlatworks.com</li>
    </ul>
    <p class="tagline">Custom Interior &amp; Exterior Window<br>Treatments By Appointment</p>
  </section>

</main>
</body>
</html>
```